Financial Coaching biz needs modern service presentation menu

We need a PowerPoint presentation document with a modern, easy-to-read layout to share with potential clients.

I have a website under development that can be used as a reference www.brightcoinharbor.com.

We'd like the doc to be simple to edit because services and verbiage will likely be modified periodically.

Two logo variations have been included.

Target Market(s)

Gen X, Gen Y, and Millienials

Industry/Entity Type

Financial Planning

Colors
85cae6
cadf82
ffffff
dddddd
cfcfcf
cee9f5

```html
<!DOCTYPE html>
<html lang="en">
<head>
<meta charset="utf-8">
<title>BrightCoin Harbor – Our Promise</title>
<link rel="stylesheet" href="https://fonts.googleapis.com/css2?family=Fira+Sans:wght@600&display=swap">
<style>
  :root {
    --white: #ffffff;
    --band-light: #d4d3d4;
    --panel-grey: #808083;
    --text-ice: #cee9f5;
    --seal-ice: #cfe8f4;
    --brand-blue: #29a8e0;
    --mascot-grey: #e2e2e3;
  }
  * { margin: 0; padding: 0; box-sizing: border-box; }
  html, body {
    width: 1200px;
    height: 848px;
    overflow: hidden;
    background: var(--white);
  }
  .slide {
    position: relative;
    width: 1200px;
    height: 848px;
    background: var(--white);
    font-family: "Fira Sans", sans-serif;
    font-weight: 600;
  }
  .brand {
    position: absolute;
    left: 70px;
    top: 38px;
    display: flex;
    align-items: center;
    gap: 22px;
  }
  .brand-mark {
    width: 88px;
    height: 116px;
    border-radius: 44px 44px 40px 40px;
    background: var(--mascot-grey);
  }
  .brand-name {
    font-size: 46px;
    line-height: 54px;
    color: var(--brand-blue);
    letter-spacing: 0;
  }
  .mascot-decoration {
    position: absolute;
    left: 764px;
    top: 0;
    width: 424px;
    height: 214px;
  }
  .band {
    position: absolute;
    left: 0;
    width: 1200px;
    background: var(--band-light);
  }
  .band-top { top: 214px; height: 18px; }
  .band-bottom { top: 768px; height: 16px; }
  .promise-panel {
    position: absolute;
    left: 0;
    top: 232px;
    width: 1200px;
    height: 536px;
    background: var(--panel-grey);
  }
  .guarantee-seal {
    position: absolute;
    left: 76px;
    top: 120px;
    width: 296px;
    height: 296px;
    border-radius: 50%;
    background: var(--seal-ice);
  }
  .promise-copy {
    position: absolute;
    left: 420px;
    top: 68px;
    width: 736px;
    color: var(--text-ice);
    font-size: 19px;
    line-height: 25.6px;
    letter-spacing: 0.9px;
    text-align: center;
    white-space: nowrap;
  }
  .promise-copy p + p { margin-top: 25.6px; }
</style>
</head>
<body>
<main class="slide">
  <header class="brand">
    <div class="brand-mark" role="img" aria-label="Brand mascot illustration"></div>
    <div class="brand-name">BRIGHTCOIN<br>HARBOR</div>
  </header>

  <svg class="mascot-decoration" viewBox="0 0 424 214" role="img" aria-label="Large decorative mascot illustration">
    <path d="M8 0 H420 V120 Q400 200 360 214 H60 Q0 150 8 0 Z" fill="var(--mascot-grey)"/>
  </svg>

  <div class="band band-top"></div>

  <section class="promise-panel">
    <div class="guarantee-seal" role="img" aria-label="Satisfaction guarantee stamp"></div>

    <div class="promise-copy">
      <p>We provide a FREE CONSULTATION and conduct a full assessment<br>before we take on any new client.&nbsp; Therefore, prospective clients<br>find out upfront if we can actually help them.</p>
      <p>We pride ourselves on being good corporate citizens as well.&nbsp; For<br>every new household we sign, we commit<br>to providing free service to household below the poverty line.</p>
      <p>Our promise is that we won't take on or charge a client a single cent<br>unless we are ABSOLUTELY SURE<br>we can add value.</p>
      <p>Our company is fundamentally built upon the service and the help<br>we provide.<br>So if we can't help you, we won't charge you.&nbsp; PERIOD.</p>
    </div>
  </section>

  <div class="band band-bottom"></div>
</main>
</body>
</html>
```